Store Front Window Design

We have a beautiful corner store front dental practice with no window signage. Crazy I know...that's why we need your help.

The final design will be done in all vinyl unless unless you suggest a different medium (meaning we are open to some design idea like using frosted glass, etc...).

The windows provide a lot of natural light so the design needs to keep a lot of natural light coming into the office. Keep in mind vinyl is not opaque so keep the signage aesthetically pleasing and a minimalist design to allow as much natural light in as possible. The design should follow the aesthetic from our logo. or tie into at least. We want a cohesive brand aesthetic.

I submitted some general layout ideas. There is a blue banner with advertising words which we want to be used in the final version. Even though the lettering is black, in reality the letters will be a white vinyl on the outside of the window. When you submit your work, be sure to add any special instructions (aka tell me the vision for the letters is white not black, maybe gold leaf, or forested glass...stuff like that). AND YOU DO NOT HAVE TO FOLLOW MY PATTERN! YOU ARE ARTISTS AND WE ARE LOOKING FOR AN ARTISTIC EYE CATCHING PRESENTATION OF THIS INFORMATION. MAKE IT FLASHY AND ADD SOME AESTHETIC FROM THE TOOTH LOGO.

The store front is 6 windows roughly 60'' x 36'' The smaller windows below are 27'' x 36''. Around the corner there are 3 windows. they are 60'' x 27'' lower windows are 27" x 27". We would like to keep the bottom windows clear and keep the signage on the top windows, however, we are flexible.

The front 6 windows need to have this information worked into the design.

Practice name: Varden and Pellosi Dental & Orthodontics.
Phone numbers: Rosalind Varden DDS: 415.555.0187
Oskar Pellosi DDS:415.555.0243

Expertise: Dr. Varden General Dentistry & Orthodontics
Dr. Pellosi Oral Surgery & Sedation

Address: 1938 Birchwood Ave

A banner across the bottom of the top windows with some key advertisement words: "Clearmold" "Braces" "Implants" "Whiting" "Call today" "Free Consultation" "Oral Surgery" "Sedation". We like the two color idea. Its up to you to decide on the color combo. I used a Dark and light blue, but maybe a Blue and grey would nice to tire in the logo colors?

I have made some mock ideas to get the ball rolling but you do not have to stick to these designs at all, just as long as all the required information is there. Be creative with the layouts, fonts, color scheme, (just remember these are going on windows not necessarily a white background), and graphics/artistic flare (refer to logo for layout inspiration and use the logo as an actual graphic). We are running a miltimillion dollar dental practice so we want these windows to be eye catching to pull in patients and look like a million dollar design. Also all 6 windows dont need ot be used. I am really looking for creative design marketing.

The corner 3 windows need the following information: name, expertise, phone number, banner.

Dr. Varden, General Dentistry & Orthodontics, 415.555.0187
Dr. Pellosi, Oral Surgery & Sedation, 415.555.0243

There is also a front door that needs to be designed. The door is 60'' x 36'' (standard door size) We want simple white vinyl on the outside of the door. We need you to organize the information on the door, pick a easy to read font, maybe use the logo and use some of the front window signage aesthetic? Its up to you...but we we were initially thinking of just making the litters white and keep it simple but again you are the designers.

Practice name: Varden and Pellosi General Dentistry & Orthodontics

Address: 1938 Birchwood Ave

Phone numbers: Dr. Varden 415.555.0187
Dr. Pellosi 415.555.0243

Hours of operation: Mon: call for an appointment
Tues-Thurs: 9am-5pm
Sat: call for an appointment
Sun: Closed

A line saying we speak Spanish: Se Habla Espanol

*****************************************************************************************************
here are some design that we liked and some rough sketches I made to start the ball rolling. Keep in mind that there are 9 windows for the front because its a corner office, but not all of them have to have stuff on it. We want simple, streamline, classy high commanding price point aesthetic. I am hiring you for your artistic minds.

Target Market(s)

anyone who has dental needs

Industry/Entity Type

Dental

Font styles to use
Serif
Sans Serif

Colors

Designer to choose colors to be used in the design.

Requirements
Must have
• 1. The required information (see project description)
• 2. Logo
• 3. Advertisement banner running along the bottom of all 9 windows (6 in front and 3 on the side)
• NOTE: Look at pictures of the store to get a sense of the customers point of view and also as a reference to how your design will be broken up across several windows or maybe you design something special for every window. But we want the banner to run along all the windows to lead customs to the door on the side. Finally the letters will be done in white vinyl unless state otherwise, remember the window needs to let in natural light so the entire window can not be covered in vinyl.
Nice to have
• artistic flare yet simple and sleep and expensive looking aesthetic. work logo into the design.
Should not have
• The goal is to catch someone eye and give them important information about the practice.
• It should not just be words.
• It should not have to many words
• It must be readable font for cards driving by.

```html
<!DOCTYPE html>
<html lang="en">
<head>
<meta charset="utf-8">
<title>Varden and Pellosi Dental &amp; Orthodontics – Window Signage</title>
<link rel="stylesheet" href="https://fonts.googleapis.com/css2?family=Bebas+Neue&family=Oswald:wght@300;400&family=Montserrat:wght@400;500;700&family=Nunito+Sans:wght@400;600&display=swap">
<style>
  :root {
    --page-bg: #e4e4e4;
    --brand-blue: #1b79c9;
    --text-blue: #1a6dba;
    --corner-grey: #8c8c8e;
    --text-grey: #6e6e70;
    --white: #ffffff;
    --ink: #1e1e1e;
  }
  * { margin: 0; padding: 0; box-sizing: border-box; }
  html, body { width: 1200px; height: 2632px; overflow: hidden; }
  body { background: var(--page-bg); position: relative; font-family: "Nunito Sans", sans-serif; }

  .window-panel {
    position: absolute; left: 100px; top: 700px;
    width: 1000px; height: 1073px;
    box-shadow: 0 14px 22px rgba(0,0,0,0.22);
    overflow: hidden;
  }
  .panel-art {
    position: absolute; left: 0; top: 0;
    width: 550px; height: 590px;
    transform: scale(1.8182); transform-origin: 0 0;
  }
  .panel-backdrop { position: absolute; inset: 0; }

  .practice-name { position: absolute; left: 0; width: 550px; top: 58px; text-align: center; }
  .practice-name .name-line {
    font-family: "Montserrat", sans-serif; font-weight: 500; font-size: 9px;
    letter-spacing: 2.6px; color: var(--text-blue); text-transform: uppercase;
  }
  .practice-name .specialty-line {
    font-family: "Montserrat", sans-serif; font-weight: 500; font-size: 11px;
    color: var(--text-grey); text-transform: uppercase; letter-spacing: 0.4px; margin-top: 1px;
  }

  .street-address {
    position: absolute; left: 68px; width: 460px; top: 118px;
    display: flex; justify-content: space-between;
    font-family: "Bebas Neue", sans-serif; font-size: 56px; line-height: 1;
    color: var(--text-blue);
  }
  .address-rule { position: absolute; left: 68px; width: 458px; top: 182px; height: 6px;
    border-top: 1.5px solid var(--brand-blue); border-bottom: 1.5px solid var(--brand-blue); }

  .emblem-area { position: absolute; left: 0; top: 228px; width: 180px; height: 182px;
    background: linear-gradient(180deg, rgba(27,121,201,0.55), rgba(27,121,201,0.25)); }

  .doctor { position: absolute; top: 232px; width: 170px; text-align: center; }
  .doctor-varden { left: 190px; }
  .doctor-pellosi { left: 372px; }
  .doctor-name { font-family: "Oswald", sans-serif; font-weight: 400; font-size: 25px; color: var(--text-blue); line-height: 1.1; }
  .doctor-specialty { margin-top: 6px; font-size: 13.5px; line-height: 17px; color: var(--text-grey); }
  .doctor-phone { margin-top: 10px; font-family: "Oswald", sans-serif; font-weight: 300; font-size: 26px; color: var(--text-blue); letter-spacing: -0.3px; }

  .promo-band {
    position: absolute; left: 0; top: 409px; width: 550px; height: 28px;
    background: var(--brand-blue);
    display: flex; align-items: center; justify-content: space-around;
  }
  .promo-band::before, .promo-band::after {
    content: ""; position: absolute; left: 0; right: 0;
    border-top: 1px dashed rgba(255,255,255,0.8);
  }
  .promo-band::before { top: 3px; }
  .promo-band::after { bottom: 3px; }
  .promo-band span {
    font-family: "Montserrat", sans-serif; font-size: 11px; font-weight: 500;
    color: var(--white); text-transform: uppercase; letter-spacing: 0.2px;
  }

  .promo-icon { position: absolute; top: 466px; }
  .icon-patient { left: 58px; width: 56px; height: 54px; background: var(--brand-blue); opacity: 0.85; }
  .icon-phone { left: 247px; width: 56px; height: 56px; }
  .icon-consult { left: 427px; width: 60px; height: 54px; background: var(--brand-blue); opacity: 0.85; }

  .panel-caption {
    position: absolute; left: 0; width: 1200px; top: 1860px; text-align: center;
    font-family: "Montserrat", sans-serif; font-weight: 700; font-size: 36px;
    color: var(--ink); letter-spacing: 1px;
  }
</style>
</head>
<body>
  <section class="window-panel">
    <div class="panel-art">
      <svg class="panel-backdrop" viewBox="0 0 550 590" width="550" height="590" aria-hidden="true">
        <rect x="0" y="0" width="550" height="300" fill="var(--brand-blue)"/>
        <rect x="0" y="300" width="550" height="290" fill="var(--corner-grey)"/>
        <circle cx="275" cy="305" r="335" fill="var(--white)"/>
      </svg>

      <div class="practice-name">
        <div class="name-line">Varden and Pellosi</div>
        <div class="specialty-line">Dental &amp; Orthodontics</div>
      </div>

      <div class="street-address"><span>1938</span><span>Birchwood</span><span>Avenue</span></div>
      <div class="address-rule"></div>

      <div class="emblem-area" role="img" aria-label="Blue caduceus emblem with wings and a tooth-shaped staff"></div>

      <div class="doctor doctor-varden">
        <div class="doctor-name">DR. VARDEN</div>
        <div class="doctor-specialty">General Dentistry<br>&amp;<br>Orthodontics</div>
        <div class="doctor-phone">415.555.0187</div>
      </div>
      <div class="doctor doctor-pellosi">
        <div class="doctor-name">DR. PELLOSI</div>
        <div class="doctor-specialty">Oral Surgery<br>&amp;<br>Sedationeral Dentistry</div>
        <div class="doctor-phone">415.555.0243</div>
      </div>

      <div class="promo-band">
        <span>Accepting New Patience</span>
        <span>Call Today</span>
        <span>Free Consultation</span>
      </div>

      <div class="promo-icon icon-patient" role="img" aria-label="Pictogram of a patient in a dental chair"></div>
      <svg class="promo-icon icon-phone" viewBox="0 0 24 24" aria-hidden="true">
        <path fill="var(--brand-blue)" d="M6.62 10.79c1.44 2.83 3.76 5.14 6.59 6.59l2.2-2.2c.27-.27.67-.36 1.02-.24 1.12.37 2.33.57 3.57.57.55 0 1 .45 1 1V20c0 .55-.45 1-1 1-9.39 0-17-7.61-17-17 0-.55.45-1 1-1h3.5c.55 0 1 .45 1 1 0 1.25.2 2.45.57 3.57.11.35.03.74-.25 1.02l-2.2 2.2z"/>
        <path d="M14 6.2a4 4 0 0 1 3.8 3.8" fill="none" stroke="var(--brand-blue)" stroke-width="1.4" stroke-linecap="round"/>
        <path d="M14 2.8a7.4 7.4 0 0 1 7.2 7.2" fill="none" stroke="var(--brand-blue)" stroke-width="1.4" stroke-linecap="round"/>
      </svg>
      <div class="promo-icon icon-consult" role="img" aria-label="Pictogram of two people in a consultation at a desk"></div>
    </div>
  </section>

  <div class="panel-caption">3 WINDOWS</div>
</body>
</html>
```